Yacht, Boats, Watersports company needs a redesign of business card

Hello Designers!
We are a Boat dealership company that sells fun in the water, we sell boats, Yachts, Kayaks and also yacht WaterSport toys. We are looking to redesign our business cards in to something a little bit more sophisticated. in a way that we can make better use of our company colors. I'm attaching a zipped file containing the company 3 sets of company logo which one is an horizontal another one is a vertical and also a chromed 3d logo. Also is included two set of business cards that we use and also some designs that i think it's interesting. We use PMS 2026c Orange and PMS 7687C Blue. I would like to see at least two different options with the orange as accent and also using blue as an accent color. It's really important for the business cards to have a font option and size that is legible to most people. Our current website is wwww.coralpennant.com. Please visit if you want to have a better feeling of the Boat dealership
You can send Single sided or double side options. We are now using single sided but we may be open for a double side option if we really like the design.
Target Market(s)
Marine, boat sales, yacht sales, water toys sales/
Contact Information for Business Card
Name: Dale Whitcombe
Address: 212 North Fenwick Lane,
Dania Beach, FL 33004
Phone: 954-731-8842
Fax: 954:731-8843
Cell: 954-382-1490
Email: dw@coralpennant.com
Website: coralpennant.com
Requirements
Must have
- the current information of the business card provided.
logo
use the PMS Colors
Nice to have
- a touch of elegance and sophistication but simple
Should not have
- should not have any typography that is hard to read, the card should be simple but yet sophisticated.

```html
<!DOCTYPE html>
<html lang="en">
<head>
<meta charset="utf-8">
<title>Coral Pennant — Business Card</title>
<link rel="stylesheet" href="https://fonts.googleapis.com/css2?family=Montserrat:wght@400;500;700;800&display=swap">
<style>
  :root {
    --brand-blue: #0556a6;
    --deep-blue: #1d4e8f;
    --brand-orange: #f37421;
    --paper: #ffffff;
    --backdrop: #e6e8ec;
    --ink-light: #ffffff;
  }
  * { box-sizing: border-box; margin: 0; padding: 0; }
  html, body { width: 1200px; height: 900px; overflow: hidden; }
  body {
    background: var(--backdrop);
    font-family: "Montserrat", Arial, sans-serif;
    position: relative;
  }
  .card {
    position: absolute;
    width: 700px;
    height: 400px;
    box-shadow: 0 10px 30px rgba(0,0,0,0.18);
    overflow: hidden;
  }
  /* Front */
  .card-front {
    left: 140px; top: 40px;
    background: var(--brand-blue);
    color: var(--ink-light);
  }
  .front-brand {
    position: absolute;
    left: 0; right: 0; top: 150px;
    text-align: center;
  }
  .brand-name {
    font-weight: 800;
    font-size: 40px;
    letter-spacing: 2px;
    text-transform: uppercase;
    white-space: nowrap;
  }
  .services {
    position: absolute;
    left: 0; right: 0; bottom: 70px;
    display: flex; justify-content: center; gap: 30px;
    list-style: none;
    font-size: 19px; font-weight: 500;
  }
  .services li::before {
    content: "";
    display: inline-block;
    width: 7px; height: 7px; border-radius: 50%;
    background: currentColor;
    margin-right: 8px;
    vertical-align: middle;
  }
  /* Back */
  .card-back {
    left: 360px; top: 470px;
    background: var(--paper);
    display: flex;
  }
  .back-brand {
    width: 300px;
    flex: none;
    display: flex; align-items: center; justify-content: center;
    color: var(--deep-blue);
  }
  .back-brand .brand-name { font-size: 24px; letter-spacing: 1px; }
  .back-contact {
    position: relative;
    flex: 1;
    background: var(--brand-orange);
    border-left: 5px solid var(--deep-blue);
    color: var(--ink-light);
    padding: 48px 20px 0 44px;
  }
  .back-contact::before {
    content: "";
    position: absolute;
    left: 0; top: 70px;
    border-top: 9px solid transparent;
    border-bottom: 9px solid transparent;
    border-left: 10px solid var(--deep-blue);
  }
  .person-name { font-size: 32px; font-weight: 700; line-height: 1.1; white-space: nowrap; }
  .person-role { font-size: 18px; font-weight: 500; margin-bottom: 30px; }
  .address { font-style: normal; font-size: 17px; line-height: 1.35; }
  .rule { width: 56px; height: 2px; background: var(--ink-light); margin: 12px 0 10px; border: 0; }
  .contact-list { list-style: none; font-size: 16px; line-height: 1.55; }
  .contact-list li { display: flex; align-items: center; gap: 10px; white-space: nowrap; }
  .contact-list svg { width: 14px; height: 14px; flex: none; }
</style>
</head>
<body>

<section class="card card-front" aria-label="Card front">
  <div class="front-brand">
    <span class="brand-name">Coral Pennant</span>
  </div>
  <ul class="services">
    <li>Marine</li>
    <li>boat sales</li>
    <li>yacht sales</li>
    <li>water toys sales</li>
  </ul>
</section>

<section class="card card-back" aria-label="Card back">
  <div class="back-brand">
    <span class="brand-name">Coral Pennant</span>
  </div>
  <div class="back-contact">
    <h1 class="person-name">Dale Whitcombe</h1>
    <p class="person-role">Owner</p>
    <address class="address">212 North Fenwick Lane,<br>Dania Beach, FL 33004</address>
    <hr class="rule">
    <ul class="contact-list">
      <li><svg viewBox="0 0 14 14" aria-hidden="true"><rect x="3.5" y="1" width="7" height="12" rx="1.2" fill="none" stroke="#fff" stroke-width="1.4"/></svg>954-731-8842</li>
      <li><svg viewBox="0 0 14 14" aria-hidden="true"><rect x="3" y="1" width="8" height="4" fill="#fff"/><rect x="1" y="5" width="12" height="6" rx="1" fill="#fff"/><rect x="3.5" y="9" width="7" height="4" fill="#fff" stroke="#f37421"/></svg>954:731-8843</li>
      <li><svg viewBox="0 0 14 14" aria-hidden="true"><path d="M3 1.5l2.5 2.5-1.4 1.8a8 8 0 0 0 4.1 4.1l1.8-1.4 2.5 2.5-1.6 1.6C6.5 12.6 1.4 7.5 1.4 3.1z" fill="#fff"/></svg>954-382-1490</li>
      <li><svg viewBox="0 0 14 14" aria-hidden="true"><rect x="1" y="3" width="12" height="8" fill="#fff"/><path d="M1 3l6 5 6-5" fill="none" stroke="#f37421" stroke-width="1.2"/></svg>dw@coralpennant.com</li>
      <li><svg viewBox="0 0 14 14" aria-hidden="true"><circle cx="7" cy="7" r="6" fill="none" stroke="#fff" stroke-width="1.4"/><path d="M1 7h12M7 1c-3 3.5-3 8.5 0 12M7 1c3 3.5 3 8.5 0 12" fill="none" stroke="#fff" stroke-width="1"/></svg>www.coralpennant.com</li>
    </ul>
  </div>
</section>

</body>
</html>
```